Sales Flyer for Outdoor Kitchens

Looks to have a trifold flyer designed based off website content / projects. Use www.backyardhearthworks.com for content

```html
<!DOCTYPE html>
<html lang="en">
<head>
<meta charset="utf-8">
<title>Backyard Hearthworks – Trifold Flyer</title>
<link href="https://fonts.googleapis.com/css2?family=Abril+Fatface&family=Poppins:wght@600;700&display=swap" rel="stylesheet">
<style>
  :root {
    --leaf: #45770a;
    --leaf-bright: #3fb83a;
    --brand-green: #36a535;
    --paper: #ececec;
    --white: #ffffff;
    --ink: #111111;
    --overlay: rgba(64, 104, 6, 0.82);
  }
  * { box-sizing: border-box; margin: 0; padding: 0; }
  html, body { width: 1200px; height: 851px; overflow: hidden; background: var(--paper); }
  .flyer {
    position: relative; width: 1200px; height: 851px; overflow: hidden;
    background: radial-gradient(circle at 30% 40%, #f4f4f4, #e2e2e2 80%);
    font-family: "Poppins", sans-serif;
  }
  .decor { position: absolute; inset: 0; width: 1200px; height: 851px; }

  /* middle panel */
  .panel-contact {
    position: absolute; left: 391px; top: 0; width: 406px; height: 851px;
    background: linear-gradient(180deg, #6f7a1c 0%, #4d7412 35%, #3f6c10 60%, #35600e 100%);
  }
  .panel-contact::after {
    content: ""; position: absolute; inset: 0; background: var(--overlay); opacity: .35;
  }

  /* about panel */
  .lamp-art {
    position: absolute; left: 95px; top: 0; width: 192px; height: 203px;
    background: radial-gradient(ellipse at 50% 80%, #d49a66 0%, #9a6440 45%, rgba(154,100,64,0) 72%);
  }
  .about-title {
    position: absolute; left: 0; top: 232px; width: 391px; text-align: center;
    font-family: "Abril Fatface", serif; font-size: 40px; color: var(--leaf); line-height: 1;
  }
  .about-title::before, .about-title::after {
    content: ""; display: inline-block; width: 56px; height: 4px; background: var(--leaf);
    vertical-align: middle; margin: 0 14px; border-radius: 50%;
  }
  .who-band {
    position: absolute; left: 0; top: 294px; width: 391px; height: 65px;
    background: var(--leaf); color: var(--white);
    font-family: "Abril Fatface", serif; font-size: 36px; line-height: 65px; text-align: center;
  }
  .about-copy {
    position: absolute; left: 10px; top: 398px; width: 371px; text-align: center;
    font-weight: 600; font-size: 16.4px; line-height: 28.3px; color: var(--ink);
  }

  /* contact panel */
  .contact-title {
    position: absolute; left: 391px; top: 172px; width: 406px; text-align: center;
    font-family: "Abril Fatface", serif; font-size: 40px; color: var(--white);
    text-shadow: 0 2px 3px rgba(0,0,0,.4);
  }
  .contact-box {
    position: absolute; left: 421px; top: 250px; width: 348px; height: 169px;
    border: 3px dotted var(--white);
    background: rgba(35, 60, 8, 0.35);
    color: var(--white); font-weight: 600; font-size: 15.5px; line-height: 20px;
  }
  .contact-row { position: absolute; left: 48px; right: 6px; }
  .contact-row svg { position: absolute; left: -38px; top: 2px; }
  .row-address { top: 14px; }
  .row-phone { top: 86px; }
  .row-mail { top: 137px; font-size: 15px; }

  .follow-title {
    position: absolute; left: 391px; top: 768px; width: 460px; text-align: center;
    font-family: "Abril Fatface", serif; font-size: 22px; color: var(--white);
  }
  .social { position: absolute; top: 810px; width: 28px; height: 28px; border-radius: 50%; background: var(--white); }

  /* cover panel */
  .brand-name {
    position: absolute; left: 850px; top: 130px; width: 320px; text-align: center;
    font-weight: 700; font-size: 30px; line-height: 34px; color: var(--brand-green);
  }
  .brand-name .brand-dot {
    display: block; width: 18px; height: 18px; border-radius: 50%; background: var(--brand-green);
    margin: 0 auto 10px;
  }
  .cover-headline {
    position: absolute; left: 800px; top: 712px; width: 400px; text-align: center;
    font-family: "Abril Fatface", serif; font-size: 34px; line-height: 44px; color: var(--white);
  }
  .cover-headline .accent { color: var(--leaf-bright); }
</style>
</head>
<body>
<div class="flyer">

  <section class="panel-contact" role="img" aria-label="Backyard patio with pavilion, fire pit and lawn under a green tint"></section>

  <svg class="decor" viewBox="0 0 1200 851" aria-hidden="true">
    <defs>
      <linearGradient id="coverPhoto" x1="0" y1="0" x2="0" y2="1">
        <stop offset="0" stop-color="#6c8a4a"/>
        <stop offset="0.35" stop-color="#8d9a7a"/>
        <stop offset="0.6" stop-color="#9b8670"/>
        <stop offset="1" stop-color="#2f3234"/>
      </linearGradient>
    </defs>
    <!-- corner and accent circles -->
    <circle cx="0" cy="-12" r="120" fill="#fff"/>
    <circle cx="0" cy="-12" r="100" fill="var(--leaf)"/>
    <circle cx="0" cy="870" r="118" fill="#fff"/>
    <circle cx="0" cy="870" r="98" fill="var(--leaf)"/>
    <circle cx="392" cy="85" r="55" fill="#fff"/>
    <circle cx="392" cy="85" r="35" fill="var(--leaf)"/>
    <circle cx="392" cy="789" r="123" fill="#fff"/>
    <circle cx="392" cy="789" r="102" fill="var(--leaf)"/>
    <circle cx="797" cy="42" r="123" fill="#fff"/>
    <circle cx="797" cy="42" r="102" fill="var(--leaf)"/>
    <!-- cover photo circle -->
    <circle cx="1092" cy="652" r="384" fill="#fff"/>
    <circle cx="1092" cy="652" r="364" fill="url(#coverPhoto)" role="img" aria-label="Covered outdoor kitchen pavilion with fireplace, grill and bar seating among trees"/>
  </svg>

  <div class="lamp-art" role="img" aria-label="Copper pendant lamp hanging from a cord"></div>
  <h2 class="about-title">ABOUT US</h2>
  <h3 class="who-band">WHO WE ARE</h3>
  <p class="about-copy">With over a decade of experience in the industry, Daniel Whitacre, the owner and operator of BHW, has become a well-known name in the Houston area. His passion for outdoor living spaces, coupled with his keen eye for design and attention to detail, has led him to create some of the most stunning and functional outdoor spaces for his clients.</p>

  <h2 class="contact-title">CONTACT US</h2>
  <div class="contact-box">
    <div class="contact-row row-address">
      <svg width="14" height="18" viewBox="0 0 14 18"><path d="M7 0a6 6 0 0 0-6 6c0 4.5 6 12 6 12s6-7.5 6-12a6 6 0 0 0-6-6zm0 8.5A2.5 2.5 0 1 1 7 3.5a2.5 2.5 0 0 1 0 5z" fill="#fff"/></svg>
      4820 Cedar Hollow Rd Ste 210 PMB<br>2046 Brookfield, 77,41, US
    </div>
    <div class="contact-row row-phone">
      <svg width="16" height="16" viewBox="0 0 24 24"><path d="M6.6 10.8a15.1 15.1 0 0 0 6.6 6.6l2.2-2.2a1 1 0 0 1 1-.25 11.4 11.4 0 0 0 3.6.57 1 1 0 0 1 1 1V20a1 1 0 0 1-1 1A17 17 0 0 1 3 4a1 1 0 0 1 1-1h3.5a1 1 0 0 1 1 1c0 1.25.2 2.45.57 3.57a1 1 0 0 1-.25 1z" fill="#fff"/></svg>
      555-302-7194
    </div>
    <div class="contact-row row-mail">
      <svg width="18" height="14" viewBox="0 0 18 14"><rect x="1" y="1" width="16" height="12" fill="none" stroke="#fff" stroke-width="2"/><path d="M1 1l8 7 8-7M1 13l6-6M17 13l-6-6" fill="none" stroke="#fff" stroke-width="1.6"/></svg>
      DW@backyardhearthworks.com
    </div>
  </div>

  <h3 class="follow-title">FOLLOW US</h3>
  <span class="social" style="left:575px"></span>
  <span class="social" style="left:613px"></span>
  <span class="social" style="left:652px"></span>

  <div class="brand-name"><span class="brand-dot"></span>BACKYARD<br>HEARTHWORKS</div>

  <h1 class="cover-headline">Create <span class="accent">YOUR DREAM</span><br>Backyard With Us</h1>
</div>
</body>
</html>
```